Firm Stationery Design

I need a design for stationery, including: Stationery First Page, Stationery Second Sheet, Envelope, Mailing Label for Flat Envelopes, and Business Cards

```html
<!DOCTYPE html>
<html lang="en">
<head>
<meta charset="utf-8">
<title>Harlow Legal LLC — Stationery</title>
<link rel="stylesheet" href="https://fonts.googleapis.com/css2?family=Montserrat:wght@300;400;500;600;700;800&display=swap">
<style>
:root{
  --bg:#a3a3a3;
  --bg-light:#b4b2b4;
  --ink:#1c1c1c;
  --black:#111111;
  --orange:#f5a11c;
  --white:#ffffff;
  --paper:#f7f7f7;
  --rule:#555555;
  --shadow:0 2px 5px rgba(0,0,0,.35);
}
*{box-sizing:border-box;margin:0;padding:0}
html,body{width:1200px;height:957px;overflow:hidden}
body{position:relative;background:var(--bg);font-family:"Montserrat",sans-serif;color:var(--ink)}
.zone-light{position:absolute;left:650px;top:0;width:550px;height:523px;background:var(--bg-light)}
.piece{position:absolute;box-shadow:var(--shadow)}
.white{background:var(--white)}
.dark{background:var(--black)}

/* brand name block */
.brand{display:flex;flex-direction:column;align-items:flex-start;gap:.35em}
.brand-square{width:1.6em;height:1.6em;background:var(--orange)}
.brand-name{font-weight:800;letter-spacing:.04em;line-height:1.05;text-transform:uppercase;color:var(--ink);white-space:nowrap}
.brand.on-dark .brand-name{color:var(--white)}

.contact{font-weight:400;line-height:1.45;color:var(--ink);white-space:nowrap}
.contact.ruled{border-left:1px solid var(--orange);padding-left:.8em}
.contact li{list-style:none;display:flex;align-items:center;gap:.35em}
.contact svg{width:.9em;height:.9em;fill:var(--orange);flex:none}
.on-dark-text{color:var(--white)}

.pattern{background:linear-gradient(100deg,#0a0a0a 0%,#1b1b1b 45%,#6b6b6b 72%,#cfcfcf 100%)}

/* business card front */
.card-front .brand{position:absolute;left:7px;top:9px;font-size:9px}
.card-front .person{position:absolute;right:6px;top:10px;text-align:right;border-right:3px solid var(--orange);padding-right:3px}
.card-front .person-name{font-weight:700;font-size:7.5px;color:var(--orange);letter-spacing:.03em}
.card-front .person-role{font-size:5px;color:var(--white)}
.card-front .contact{position:absolute;left:7px;top:52px;font-size:4.6px}
.card-front .panel{position:absolute;right:0;bottom:0;width:63px;height:60px;background:var(--white)}

/* letterhead */
.letterhead .brand{position:absolute;left:14px;top:9px;font-size:5.5px}
.letterhead .contact{position:absolute;left:92px;top:10px;font-size:2.6px}
.letterhead .recipient{position:absolute;left:14px;top:54px;font-size:2.6px;line-height:1.5}
.letterhead .recipient strong{font-weight:600}
.letterhead .body{position:absolute;left:14px;top:78px;width:113px;font-size:2.5px;line-height:1.7;color:#444}
.letterhead .body p{margin-bottom:4px;text-align:justify}
.letterhead .closing{position:absolute;left:14px;top:155px;font-size:2.6px;line-height:1.6}
.letterhead .sign-line{width:22px;height:6px;border-bottom:.5px solid #333;margin:2px 0}

/* envelopes */
.env-back .brand{position:absolute;left:8px;top:9px;font-size:5.5px}
.env-back .contact{position:absolute;left:44px;top:10px;font-size:3.4px}
.env-flap .flap{position:absolute;left:0;top:0;width:210px;height:35px}
.env-flap .brand{position:absolute;left:50%;top:8px;transform:translateX(-50%);font-size:6px;align-items:center}

/* notebook */
.notebook-cover .rings{position:absolute;left:-4px;top:4px;width:8px;height:192px;background:radial-gradient(circle at 4px 4px,#222 2px,transparent 2.4px) 0 0/8px 10px repeat-y}
.notebook-frame{position:absolute;left:256px;top:287px;width:377px;height:236px;border:1px solid #9a9a9a}
.notebook-open{position:absolute;left:302px;top:311px;width:280px;height:197px;display:flex;box-shadow:var(--shadow)}
.page{position:relative;flex:1;background:var(--paper)}
.page+.page{border-left:3px solid #2a2a2a}
.page .brand{position:absolute;left:7px;top:6px;font-size:4.5px}
.page .date{position:absolute;right:6px;top:14px;font-size:4.3px;color:#333}
.page .lines{position:absolute;left:7px;right:6px;top:32px;height:152px;background:repeating-linear-gradient(to bottom,transparent 0,transparent 7px,var(--rule) 7px,var(--rule) 8px)}

/* folder */
.folder-panel{position:absolute;width:140px;height:180px;box-shadow:var(--shadow)}
.folder-cover-front .brand{position:absolute;left:16px;top:28px;font-size:13px}
.folder-cover-front .contact{position:absolute;left:16px;bottom:14px;font-size:5px}
.folder-cover-back .panel{position:absolute;left:26px;top:30px;width:58px;height:100px;background:var(--white)}
.folder-inside-left{background:#e4e4e4}
.folder-inside-left .pocket{position:absolute;left:0;bottom:0;width:100%;height:48px;background:var(--black);border-radius:0 14px 0 0}
.folder-inside-right{background:#ececec}
.folder-inside-right .insert{position:absolute;left:14px;top:10px;width:116px;height:150px;background:var(--white);box-shadow:0 1px 3px rgba(0,0,0,.25)}
.folder-inside-right .insert .brand{position:absolute;left:9px;top:8px;font-size:4.5px}
.folder-inside-right .insert .contact{position:absolute;left:70px;top:8px;font-size:2.2px}
.folder-inside-right .insert .text{position:absolute;left:9px;top:40px;width:96px;font-size:2.3px;line-height:1.7;color:#444}
.folder-inside-right .pocket{position:absolute;left:0;bottom:0;width:100%;height:48px;background:var(--orange);border-radius:14px 0 0 0}

/* bottom row */
.big-env .brand{position:absolute;left:25px;top:24px;font-size:11px}
.big-env .contact{position:absolute;left:91px;top:26px;font-size:9px;color:#444}
.second-sheet .brand{position:absolute;left:16px;top:16px;font-size:9.5px}
.second-sheet .contact{position:absolute;left:65px;top:17px;font-size:6.8px;color:#444}
.comp-slip .brand{position:absolute;left:9px;top:12px;font-size:14px}
.comp-slip .contact{position:absolute;right:9px;top:32px;font-size:5.5px}
.comp-slip .compliments{position:absolute;right:11px;bottom:10px;font-size:11px;font-weight:400}
.comp-slip .compliments span{color:var(--orange)}
</style>
</head>
<body>
<div class="zone-light"></div>

<!-- business card back -->
<div class="piece pattern" style="left:77px;top:77px;width:166px;height:95px" role="img" aria-label="Business card back: repeating brand pattern fading from black to light grey"></div>

<!-- business card front -->
<div class="piece dark card-front" style="left:77px;top:185px;width:166px;height:94px">
  <div class="brand on-dark"><div class="brand-square"></div><div class="brand-name">Harlow Legal</div></div>
  <div class="person"><div class="person-name">DANIEL REEVE</div><div class="person-role">Managing Director</div></div>
  <ul class="contact on-dark-text">
    <li>Your address, City</li>
    <li style="margin-bottom:2px">State, Zip 1234</li>
    <li><svg viewBox="0 0 10 10"><path d="M2 1h2l1 2.5-1.3 1a6 6 0 0 0 2.8 2.8l1-1.3L10 7v2a1 1 0 0 1-1 1A9 9 0 0 1 0 1a1 1 0 0 1 1-1z"/></svg>123 456 789</li>
    <li><svg viewBox="0 0 10 10"><path d="M0 2h10v6H0zM0 2l5 3.5L10 2"/></svg>info@harlowlegalllc.com</li>
    <li><svg viewBox="0 0 10 10"><circle cx="5" cy="5" r="5"/></svg>www.harlowlegalllc.com</li>
  </ul>
  <div class="panel"></div>
</div>

<!-- letterhead -->
<div class="piece white letterhead" style="left:257px;top:78px;width:141px;height:200px">
  <div class="brand"><div class="brand-square"></div><div class="brand-name">Harlow Legal</div></div>
  <ul class="contact ruled">
    <li>Your address, City</li>
    <li>State, Zip 1234</li>
    <li><svg viewBox="0 0 10 10"><circle cx="5" cy="5" r="5"/></svg>123 456 789</li>
    <li><svg viewBox="0 0 10 10"><circle cx="5" cy="5" r="5"/></svg>info@harlowlegalllc.com</li>
    <li><svg viewBox="0 0 10 10"><circle cx="5" cy="5" r="5"/></svg>www.harlowlegalllc.com</li>
  </ul>
  <div class="recipient"><strong>MAREN HOLT</strong><br>Chief Executive Officer<br>City State, Zip Code</div>
  <div class="body">
    <p>Thank you for meeting with our team last week. We have reviewed the documents you shared and prepared a summary of the next steps for your matter, including timelines and the filings we expect to make this quarter.</p>
    <p>Please read the enclosed notes carefully and let us know if any details need correction before we proceed.</p>
    <p>We look forward to working with you and will be in touch again shortly with further updates.</p>
  </div>
  <div class="closing">Sincerely,<div class="sign-line"></div>Owen Pratt</div>
</div>

<!-- envelope back -->
<div class="piece white env-back" style="left:412px;top:79px;width:209px;height:90px">
  <div class="brand"><div class="brand-square"></div><div class="brand-name">Harlow<br>Legal</div></div>
  <ul class="contact ruled"><li>Your address, City</li><li>State, Zip 1234</li></ul>
</div>

<!-- envelope flap -->
<div class="piece white env-flap" style="left:409px;top:185px;width:210px;height:92px">
  <svg class="flap" viewBox="0 0 210 35" preserveAspectRatio="none"><path d="M0 0H210L203 26Q201 33 193 33H17Q9 33 7 26Z" fill="#111"/></svg>
  <div class="brand on-dark"><div class="brand-name">Harlow Legal</div></div>
</div>

<!-- notebook cover -->
<div class="piece pattern notebook-cover" style="left:78px;top:309px;width:140px;height:200px" role="img" aria-label="Notebook cover: repeating brand pattern fading from black to light grey">
  <div class="rings"></div>
</div>

<!-- notebook open -->
<div class="notebook-frame"></div>
<div class="notebook-open">
  <div class="page">
    <div class="brand"><div class="brand-square"></div><div class="brand-name">Harlow Legal</div></div>
    <div class="date">Date....../....../......</div>
    <div class="lines"></div>
  </div>
  <div class="page">
    <div class="brand"><div class="brand-square"></div><div class="brand-name">Harlow Legal</div></div>
    <div class="date">Date....../....../......</div>
    <div class="lines"></div>
  </div>
</div>

<!-- folder outside -->
<div class="folder-panel white folder-cover-front" style="left:775px;top:50px">
  <div class="brand"><div class="brand-square"></div><div class="brand-name">Harlow<br>Legal</div></div>
  <ul class="contact">
    <li><svg viewBox="0 0 10 10"><circle cx="5" cy="5" r="5"/></svg>123 456 789</li>
    <li><svg viewBox="0 0 10 10"><circle cx="5" cy="5" r="5"/></svg>info@harlowlegalllc.com</li>
    <li><svg viewBox="0 0 10 10"><circle cx="5" cy="5" r="5"/></svg>www.harlowlegalllc.com</li>
  </ul>
</div>
<div class="folder-panel dark folder-cover-back" style="left:915px;top:50px">
  <div class="panel"></div>
</div>

<!-- folder inside -->
<div class="folder-panel folder-inside-left" style="left:775px;top:270px">
  <div class="pocket"></div>
</div>
<div class="folder-panel folder-inside-right" style="left:915px;top:270px">
  <div class="insert">
    <div class="brand"><div class="brand-square"></div><div class="brand-name">Harlow Legal</div></div>
    <ul class="contact ruled"><li>Your address, City</li><li>State, Zip 1234</li><li>123 456 789</li><li>info@harlowlegalllc.com</li></ul>
    <div class="text">Thank you for meeting with our team. Our summary of next steps is enclosed for your review.</div>
  </div>
  <div class="pocket"></div>
</div>

<!-- large envelope -->
<div class="piece white big-env" style="left:78px;top:586px;width:356px;height:267px">
  <div class="brand"><div class="brand-square"></div><div class="brand-name">Harlow<br>Legal</div></div>
  <ul class="contact ruled"><li>Your address, City</li><li>State, Zip 1234</li></ul>
</div>

<!-- second sheet -->
<div class="piece white second-sheet" style="left:480px;top:586px;width:198px;height:264px">
  <div class="brand"><div class="brand-square"></div><div class="brand-name">Harlow<br>Legal</div></div>
  <ul class="contact ruled"><li>Your address, City</li><li>State, Zip 1234</li></ul>
</div>

<!-- pattern card -->
<div class="piece pattern" style="left:810px;top:570px;width:274px;height:129px" role="img" aria-label="Card back: repeating brand pattern fading from black to light grey"></div>

<!-- compliments slip -->
<div class="piece white comp-slip" style="left:808px;top:733px;width:275px;height:130px">
  <div class="brand"><div class="brand-square"></div><div class="brand-name">Harlow<br>Legal</div></div>
  <ul class="contact">
    <li>Your address, City</li>
    <li style="margin-bottom:3px">State, Zip 1234</li>
    <li><svg viewBox="0 0 10 10"><path d="M2 1h2l1 2.5-1.3 1a6 6 0 0 0 2.8 2.8l1-1.3L10 7v2a1 1 0 0 1-1 1A9 9 0 0 1 0 1a1 1 0 0 1 1-1z"/></svg>123 456 789</li>
    <li><svg viewBox="0 0 10 10"><path d="M0 2h10v6H0zM0 2l5 3.5L10 2"/></svg>info@harlowlegalllc.com</li>
    <li><svg viewBox="0 0 10 10"><circle cx="5" cy="5" r="5"/></svg>www.harlowlegalllc.com</li>
  </ul>
  <div class="compliments">with <span>compliments</span></div>
</div>
</body>
</html>
```